Home decoration company - sustainable wall panels

- I would need you to design 5-10 pages for my client's website.
- The design should have details of wall panels that are being sold on the website - movelterra.com.
- It should have wood + sustainability branding.
- please focus on using shapes of products that are being sold on the website and use them as design for branding

See more here
https://sheets.quorvix.net/d/7kpRtW2nLqZ8bYhMfGcVdXsJ4eTuA9wN3oHiKy5BzPl/edit?usp=sharing

Target Market(s)

people who are want sustainable home/business wall decor

Industry/Entity Type

Interior Decoration

Logo Text

Movel Terra (for favicon, "MT")

Number of Pages Required

5+ page

Font styles to use
Serif
Sans Serif

Requirements
Must have
• - details of products that are being sold on the website movelterra.com (you will see there are different wall panel shapes)
- great creative design ideas
- follow instructions from here https://sheets.quorvix.net/d/7kpRtW2nLqZ8bYhMfGcVdXsJ4eTuA9wN3oHiKy5BzPl/edit?usp=sharing
- the design must be at least 2 levels above the current one on movelterra.com
- use photos from here https://files.quorvix.net/folders/5tWmQeRb8YuNc2XkLpAsDv3ZhGj7FiO-?usp=sharing
Nice to have
• - it would be nice if you would give your own creative suggestions
Should not have
• - should not look like it's a 1990s website

```html
<!DOCTYPE html>
<html lang="en">
<head>
<meta charset="utf-8">
<title>Movel Terra – Contact</title>
<link href="https://fonts.googleapis.com/css2?family=Oswald:wght@500;600&family=Poppins:wght@400;500;600&display=swap" rel="stylesheet">
<style>
:root{
  --bark:#2e1a08;
  --umber:#3a2410;
  --rust:#7b3f00;
  --rust-text:#8a4a0c;
  --paper:#f1efec;
  --field:#e4e3e2;
  --ink:#444;
  --white:#fff;
}
*{box-sizing:border-box;margin:0;padding:0}
html,body{width:1047px;height:1200px;overflow:hidden}
body{position:relative;font-family:'Poppins',sans-serif;color:var(--ink);background:var(--paper)}
.topbar{position:absolute;left:0;top:0;width:100%;height:26px;background:var(--bark);color:var(--white);font-size:9.5px;display:flex;align-items:center;justify-content:space-between;padding:0 77px}
.topbar .info{display:flex;gap:20px;align-items:center}
.topbar .info span{display:flex;align-items:center;gap:5px}
.header{position:absolute;left:0;top:26px;width:100%;height:67px;background:var(--white)}
.brand{position:absolute;left:78px;top:4px;width:86px;height:59px;border:3px solid var(--umber);display:flex;align-items:center;justify-content:center;gap:4px;font-family:'Poppins',sans-serif;font-weight:500;font-size:10.5px;color:var(--umber)}
.brand i{width:8px;height:8px;background:var(--umber);display:block}
.nav{position:absolute;right:77px;top:0;height:67px;display:flex;align-items:center;gap:24px;font-family:'Oswald',sans-serif;font-weight:500;font-size:11.5px;color:var(--bark);text-transform:uppercase}
.nav .active{color:var(--rust-text)}
.hero{position:absolute;left:0;top:93px;width:100%;height:680px;background:radial-gradient(ellipse at 78% 45%,#a8712e 0%,#6a4520 30%,#3b2612 60%,#24160a 100%)}
.hero h1{position:absolute;left:0;width:100%;top:118px;text-align:center;font-family:'Oswald',sans-serif;font-weight:600;font-size:38px;color:var(--white);letter-spacing:-.5px}
.hero p{position:absolute;left:0;width:100%;top:163px;text-align:center;font-size:15.5px;color:var(--white)}
.field{position:absolute;left:262px;width:523px;background:var(--white);font-size:13.5px;font-weight:500;color:#555;padding:14px 22px}
.submit{position:absolute;background:var(--rust);color:var(--white);font-weight:600;display:flex;align-items:center;justify-content:center}
.footer{position:absolute;left:0;top:773px;width:100%;height:427px;background:linear-gradient(180deg,#f3f1ee,#ece9e5)}
.footer-brand{position:absolute;left:78px;top:106px;width:177px;height:122px;border:4px solid var(--umber);display:flex;align-items:center;justify-content:center;gap:6px;font-weight:500;font-size:19px;color:var(--umber);background:#e9e2da}
.footer-brand i{width:12px;height:12px;background:var(--umber);display:block}
.col{position:absolute;top:96px}
.col h2{font-family:'Oswald',sans-serif;font-weight:600;font-size:22px;color:var(--bark);line-height:26px;margin-bottom:6px}
.col ul{list-style:none;font-size:11.5px;line-height:21px}
.contact-line{display:flex;gap:6px;font-size:11.5px;line-height:17px;margin-bottom:4px}
.contact-line svg{flex:none;margin-top:4px}
.socials{display:flex;gap:10px;margin-top:11px;margin-left:6px}
.socials span{width:12px;height:12px;border:2px solid var(--rust-text);border-radius:2px}
.mini{position:absolute;left:723px;width:212px;background:var(--field);font-size:9.5px;padding:0 13px;display:flex;align-items:flex-start;padding-top:9px}
.rule{position:absolute;left:78px;top:377px;width:891px;height:1px;background:#c8c4c0}
.copy{position:absolute;left:0;width:100%;top:396px;text-align:center;font-size:14px;color:#333}
.totop{position:absolute;left:988px;top:362px;width:29px;height:29px;border-radius:50%;background:var(--bark);display:flex;align-items:center;justify-content:center}
</style>
</head>
<body>
<div class="topbar">
  <span>Ordering larger quantities? Call us.</span>
  <div class="info">
    <span><svg width="8" height="8" viewBox="0 0 10 10"><path d="M2 0l2 2.5-1 1.3a6 6 0 0 0 3.2 3.2l1.3-1L10 8l-1.5 2A9 9 0 0 1 0 1.5z" fill="#c86a1a"/></svg>phone number : &nbsp;+1 555 014 3270</span>
    <span><svg width="9" height="7" viewBox="0 0 10 8"><rect width="10" height="8" fill="#c86a1a"/><path d="M0 0l5 4 5-4" stroke="#2e1a08" fill="none"/></svg>Email : hello@movelterra.com, orders@movelterra.com</span>
  </div>
</div>

<header class="header">
  <div class="brand"><i></i>Movel Terra</div>
  <nav class="nav">
    <span>Home</span><span>Wall Paneling</span><span>Door</span><span>Cutting Boards</span><span>Table Tops</span><span>About Us</span><span class="active">Contact Us</span>
  </nav>
</header>

<section class="hero" role="img" aria-label="Interior photo of a reclaimed wood stacked wall panel in warm light">
  <h1>KEEP IN TOUCH</h1>
  <p>Contact us by filling out the form below</p>
</section>
<div class="field" style="top:302px;height:45px">Name</div>
<div class="field" style="top:356px;height:45px">Email</div>
<div class="field" style="top:410px;height:205px;padding-top:16px">Message</div>
<div class="submit" style="left:448px;top:624px;width:152px;height:36px;font-size:15.5px">SUBMIT</div>

<footer class="footer" role="img" aria-label="Light background with a faint pattern of tree ring slices">
  <div class="footer-brand"><i></i>Movel Terra</div>
  <div class="col" style="left:305px">
    <h2>NAVIGATION</h2>
    <ul><li>Home</li><li>Wall panels</li><li>Doors</li><li>Cutting boards</li><li>About us</li></ul>
  </div>
  <div class="col" style="left:472px">
    <h2>CONTACT &nbsp;US</h2>
    <div class="contact-line"><svg width="10" height="10" viewBox="0 0 10 10"><path d="M2 0l2 2.5-1 1.3a6 6 0 0 0 3.2 3.2l1.3-1L10 8l-1.5 2A9 9 0 0 1 0 1.5z" fill="var(--rust-text)"/></svg><span>Phone number +1 555 014 3270</span></div>
    <div class="contact-line"><svg width="11" height="8" viewBox="0 0 10 8"><rect width="10" height="8" fill="var(--rust-text)"/><path d="M0 0l5 4 5-4" stroke="#f1efec" fill="none"/></svg><span>Email us : hello@movelterra.com,<br>orders@movelterra.com</span></div>
    <div class="socials"><span></span><span></span><span></span></div>
  </div>
  <div class="col" style="left:721px">
    <h2>CONTACT FORM</h2>
  </div>
  <div class="mini" style="top:133px;height:29px">Name</div>
  <div class="mini" style="top:164px;height:30px">Email</div>
  <div class="mini" style="top:197px;height:87px">Message</div>
  <div class="submit" style="left:724px;top:289px;width:80px;height:27px;font-size:10.5px">SUBMIT</div>
  <div class="rule"></div>
  <div class="copy">Copyright 2020 | All Rights Reserved</div>
  <div class="totop"><svg width="9" height="6" viewBox="0 0 9 6"><path d="M1 5l3.5-3.5L8 5" stroke="#fff" stroke-width="1.6" fill="none"/></svg></div>
</footer>
</body>
</html>
```